Looking for a modern, Professional business card design

We have a simple business card, but are looking for a more modern, professional look. A sample of the basic card is attached as well as the logo. We would also like to add that we offer:
Struggling with your finances?
- Learn to become debt free
- Discover the power of cash
- Control your money instead of it controlling you
Let us help you achieve a new level of financial freedom!
Also, we would like to have a "SPECIAL OFFER!: FREE 30 minute consultation"
Financial Planning

```html
<!DOCTYPE html>
<html lang="en">
<head>
<meta charset="utf-8">
<title>Summit Money Coaching – Business Card</title>
<link rel="stylesheet" href="https://fonts.googleapis.com/css2?family=Source+Sans+3:ital,wght@0,400;0,600;0,700;1,400;1,700&display=swap">
<style>
  :root {
    --backdrop: #3b3b3b;
    --paper: #ffffff;
    --brand-green: #4a9a3c;
    --green-light: #a9d23c;
    --green-mid: #6cb33f;
    --green-deep: #3d8a3a;
    --ink: #1f1f1f;
    --ink-soft: #555555;
    --rule: #cfcfcf;
  }
  * { box-sizing: border-box; margin: 0; padding: 0; }
  html, body {
    width: 1105px; height: 1200px; overflow: hidden;
    background: var(--backdrop);
    font-family: "Source Sans 3", "Segoe UI", sans-serif;
  }
  .card {
    position: absolute;
    left: 193px;
    width: 720px;
    height: 412px;
  }
  /* Front */
  .card-front { top: 181px; background: var(--paper); }
  .brand {
    position: absolute; left: 30px; top: 170px;
    display: flex; align-items: center; gap: 12px;
  }
  .brand-dot {
    width: 30px; height: 30px; border-radius: 50%;
    background: var(--brand-green); flex: none;
  }
  .brand-name {
    color: var(--brand-green);
    font-weight: 700; font-size: 30px; line-height: 1.05;
    text-transform: uppercase; letter-spacing: 0.5px;
  }
  .divider {
    position: absolute; left: 322px; top: 116px;
    width: 1px; height: 177px; background: var(--rule);
  }
  .contact-block { position: absolute; left: 348px; top: 126px; }
  .person-name {
    color: var(--brand-green); font-weight: 600; font-size: 25px; line-height: 1;
  }
  .person-title {
    color: var(--ink); font-size: 19px; margin-top: 6px;
  }
  .contact-list { list-style: none; margin-top: 18px; }
  .contact-list li {
    display: flex; align-items: center; gap: 9px;
    color: var(--ink-soft); font-size: 19px; line-height: 27.5px;
  }
  .contact-list svg { width: 17px; height: 17px; flex: none; fill: var(--brand-green); }
  /* Back */
  .card-back {
    top: 637px;
    background: radial-gradient(ellipse 60% 75% at 50% 42%, var(--green-light) 0%, var(--green-mid) 45%, var(--green-deep) 100%);
    color: #ffffff; text-align: center;
  }
  .back-brand {
    position: absolute; left: 0; right: 0; top: 92px;
    display: flex; justify-content: center; align-items: center; gap: 12px;
  }
  .back-brand .brand-dot { background: #ffffff; width: 34px; height: 34px; }
  .back-brand .brand-name { color: #ffffff; font-size: 36px; }
  .pitch { position: absolute; left: 0; right: 0; top: 236px; }
  .pitch-heading { font-weight: 600; font-size: 21px; text-transform: uppercase; letter-spacing: 0.2px; }
  .pitch-lines { font-style: italic; font-size: 18.5px; line-height: 26.5px; margin-top: 4px; }
  .offer { font-style: italic; font-weight: 700; font-size: 27px; margin-top: 12px; }
</style>
</head>
<body>
  <section class="card card-front" aria-label="Card front">
    <div class="brand">
      <span class="brand-dot"></span>
      <span class="brand-name">Summit Money<br>Coaching</span>
    </div>
    <div class="divider"></div>
    <div class="contact-block">
      <h1 class="person-name">Daniel R. Hayes</h1>
      <p class="person-title">Personal Financial Coach</p>
      <ul class="contact-list">
        <li>
          <svg viewBox="0 0 16 16" aria-hidden="true"><path d="M4 0h8a1.5 1.5 0 0 1 1.5 1.5v13A1.5 1.5 0 0 1 12 16H4a1.5 1.5 0 0 1-1.5-1.5v-13A1.5 1.5 0 0 1 4 0zm0.5 2v10.5h7V2zM8 13.3a.9.9 0 1 0 0 1.8.9.9 0 0 0 0-1.8z"/></svg>
          (555) 014-2387
        </li>
        <li>
          <svg viewBox="0 0 16 16" aria-hidden="true"><path d="M0 3h16v1.2L8 9 0 4.2zM0 5.8l8 4.8 8-4.8V13H0z"/></svg>
          daniel@steadypathmoney.com
        </li>
        <li>
          <svg viewBox="0 0 16 16" aria-hidden="true"><circle cx="8" cy="8" r="8"/><path d="M5 4.5c1.5 0 2 1 3 1.5s.5 1.8-.7 2-1 1.5-1.8 2.5c-.5-1-.3-2-1.3-2.6S3.8 6 5 4.5zM10.5 10c.8-.4 1.8-.2 2.2.5-.5 1-1.3 1.8-2.4 2.3.2-1-.6-2.2.2-2.8z" fill="#ffffff"/></svg>
          www.steadypathmoney.com
        </li>
      </ul>
    </div>
  </section>

  <section class="card card-back" aria-label="Card back">
    <div class="back-brand">
      <span class="brand-dot"></span>
      <span class="brand-name">Summit Money Coaching</span>
    </div>
    <div class="pitch">
      <h2 class="pitch-heading">Struggling with your finances?</h2>
      <p class="pitch-lines">
        Learn to become debt free &bull; Discover the power of cash<br>
        Control your money instead of it controlling you<br>
        Let us help you achieve a new level of financial freedom!
      </p>
      <p class="offer">SPECIAL OFFER!: FREE 30 minute consultation</p>
    </div>
  </section>
</body>
</html>
```